Home Page Design (+50 More Pages To Winning Designer!)

We have a 50+ page website, but we're starting with the home page. The winning designer will get all 50+ pages to design as a 2nd project, so make sure you do your best!

Velorane is in the private jet industry and needs a re-designed website.

We have created the structure for the website and content inside of Frandle.io (THESE ARE ONLY ROUGH A.I. GENERATED WIREFRAMES AND DO NOT NEED TO BE FOLLOWED EXACTLY) - https://www.frandle.io/app/project/K482915_qWmRtZaLs-KDnHoUvvy82QJ5cfhaR61trkwqlDV3Hm

Take the content from the 'Home Page' under the 'Wireframe' tab on the Frandle.io link above, but feel free to re-design the page in a better way as these are only A.I. generated wireframes.

We want a DARK theme.... High quality, luxurious feel, greyscale colors. Attached is a brand guideline (BUT THIS IS NOT A 100% BRAND GUIDELINE, YOU CAN CHANGE COLORS AND FONTS AND MAKE CHANGES IF YOU HAVE BETTER IDEAS) and attached is our logo. We are also attaching some examples of other apps and websites to give you a guideline of what we're looking for for this design project.

The final design MUST communicate luxury using high-quality imagery of large cabin luxurious private jets.
Updates

ENTRIES THAT DO NOT FOLLOW THE PROJECT BRIEF WILL BE AUTOMATICALLY DISCARDED. FOLLOW THE INSTRUCTIONS!

Industry/Entity Type

Travel

Number of Pages Required

1 page

Font styles to use
Sans Serif

Colors

Designer to choose colors to be used in the design.

Requirements
Must have
• Follow wireframe and use content in wireframe (see Frandle.io link)

```html
<!DOCTYPE html>
<html lang="en">
<head>
<meta charset="utf-8">
<title>Velorane — Private Jet Travel</title>
<link href="https://fonts.googleapis.com/css2?family=Saira:wght@300;400&family=Manrope:wght@400;500;600;700&display=swap" rel="stylesheet">
<style>
:root{
  --black:#050505;
  --ink:#0d0d0d;
  --band:#303030;
  --panel:#2a2a2a;
  --white:#ffffff;
  --text:#e8e8e8;
  --muted:#bdbdbd;
  --line:#8a8a8a;
  --dark-text:#151515;
}
*{box-sizing:border-box;margin:0;padding:0}
html,body{width:1200px;height:4231px;overflow:hidden;background:var(--black)}
body{font-family:"Manrope",sans-serif;color:var(--text);position:relative}
section,footer,header{position:relative;width:1200px;overflow:hidden}
.abs{position:absolute}
.display{font-family:"Saira",sans-serif;font-weight:300;text-transform:uppercase;color:var(--white);letter-spacing:.5px}
.eyebrow{font-size:10px;font-weight:500;text-transform:uppercase;letter-spacing:.4px;color:var(--white)}
.body{font-size:10.5px;line-height:15px;color:var(--text)}
.label{font-family:"Saira",sans-serif;font-size:11px;text-transform:uppercase;color:var(--white)}
.btn{position:absolute;display:flex;align-items:center;justify-content:center;font-size:10px;font-weight:700;text-transform:uppercase;letter-spacing:.5px;height:33px}
.btn-light{background:var(--white);color:var(--dark-text)}
.btn-outline{border:1px solid var(--white);color:var(--white)}
.btn-dark{background:var(--black);color:var(--white)}
.btn-outline-dark{border:1px solid var(--dark-text);color:var(--dark-text)}
.brand{font-family:"Manrope",sans-serif;font-weight:500;font-size:26px;color:var(--white);display:flex;align-items:center;gap:8px}
.brand i{display:block;width:14px;height:14px;background:var(--white)}
.photo{position:absolute}
/* hero */
.hero{height:578px;background:linear-gradient(90deg,#0a0a0a 0%,#161616 55%,#1c1c1c 100%)}
.nav a{position:absolute;top:43px;font-size:10px;font-weight:500;color:var(--white);text-decoration:none;text-transform:uppercase}
.hero .photo{left:706px;top:144px;width:494px;height:434px;background:radial-gradient(ellipse at 60% 70%,#6b5438 0%,#2a2420 35%,#111 75%)}
/* features band */
.band{height:208px;background:var(--band)}
.band .feature{position:absolute;top:46px;width:300px}
.band .feature svg{width:40px;height:40px;stroke:var(--white);fill:none;stroke-width:1.3}
/* ownership */
.ownership{height:529px;background:radial-gradient(ellipse at 95% 100%,#2a2a2a 0%,#050505 45%)}
.radio{display:flex;align-items:center;gap:7px;font-size:10px;color:var(--white)}
.radio::before{content:"";width:10px;height:10px;border-radius:50%;background:var(--white)}
/* services */
.services{height:422px;background:linear-gradient(135deg,#262626 0%,#333 60%,#2a2a2a 100%)}
.card{position:absolute;top:197px;width:315px;height:163px;border:1px solid var(--line);padding:28px}
.card svg{width:34px;height:34px;stroke:var(--white);fill:none;stroke-width:1.3;margin-bottom:14px}
/* cta light */
.cta-light{height:238px;background:linear-gradient(180deg,#fff 0%,#fff 55%,#f1f1f1 100%)}
.cta-light .photo{left:0;top:110px;width:1200px;height:128px;background:linear-gradient(90deg,#c9ccd1 0%,#e9eaec 35%,rgba(255,255,255,0) 70%)}
/* unparalleled */
.luxury{height:537px;background:radial-gradient(ellipse at 10% 100%,#222 0%,#030303 50%)}
.luxury .photo.sky{left:834px;top:0;width:366px;height:537px;background:linear-gradient(180deg,#cfd3d8 0%,#f3f4f6 40%,#b8bcc2 100%)}
.luxury .photo.jet{left:450px;top:60px;width:560px;height:360px;background:linear-gradient(150deg,rgba(160,168,180,.0) 20%,rgba(160,168,180,.35) 50%,rgba(90,98,112,.0) 80%)}
/* faq */
.faq{height:727px;background:linear-gradient(160deg,#2c2c2c 0%,#202020 100%)}
.faq .photo{left:113px;top:93px;width:334px;height:537px;background:linear-gradient(180deg,#5d6b7c 0%,#7a7f86 35%,#4a3a2c 75%,#2d2419 100%)}
.faq-item{position:absolute;left:528px;width:482px;border:1px solid var(--muted);padding:0 18px}
.faq-q{height:37px;display:flex;align-items:center;justify-content:space-between;font-size:10px;font-weight:600;text-transform:uppercase;color:var(--white)}
.faq-q b{font-size:14px;font-weight:400}
/* testimonial */
.testimonial{height:455px;background:radial-gradient(ellipse at 100% 0%,#222 0%,#030303 40%)}
.testimonial .photo{left:742px;top:51px;width:289px;height:327px;background:linear-gradient(180deg,#b9b2a4 0%,#6f6f72 45%,#3d4046 100%)}
.arrows{position:absolute;left:691px;top:345px;width:131px;height:59px;background:#3a3a3a;display:flex}
.arrows span{flex:1;display:flex;align-items:center;justify-content:center}
.arrows span+span{border-left:1px solid #777}
/* cta dark */
.cta-dark{height:257px;background:linear-gradient(90deg,#121212 0%,#2b2620 50%,#141414 100%)}
/* footer */
.footer{height:280px;background:var(--black)}
.footer h4{font-family:"Saira",sans-serif;font-weight:400;font-size:11px;text-transform:uppercase;color:var(--white);margin-bottom:6px}
.footer ul{list-style:none}
.footer li{font-size:10px;line-height:20px;color:var(--white)}
.social{position:absolute;top:4086px;width:22px;height:22px;border:1px solid var(--white);border-radius:50%}
.legal a{font-size:9.5px;color:var(--white);text-decoration:none;text-transform:uppercase}
</style>
</head>
<body>

<header class="hero">
  <div class="photo" role="img" aria-label="Private jet nose and landing gear lit at dusk on the runway"></div>
  <div class="abs brand" style="left:112px;top:32px">Velorane<i></i></div>
  <nav class="nav">
    <a style="left:381px">Aircraft</a>
    <a style="left:461px">Programs</a>
    <a style="left:552px">Why Velorane</a>
    <a style="left:662px">Lifestyle</a>
  </nav>
  <a class="btn btn-light" style="left:804px;top:31px;width:112px">Featured from blog</a>
  <a class="btn btn-outline" style="left:973px;top:31px;width:114px">Article title</a>
  <h1 class="abs display" style="left:110px;top:188px;font-size:44px;line-height:56px;width:600px">Experience the ultimate<br>in luxury jet travel</h1>
  <p class="abs body" style="left:113px;top:305px;width:500px;font-size:11px">Velorane offers fractional jet ownership, jet card programs, private jet lease programs, all access programs, helicopter access programs, and by the seat charter flights. Discover the perfect flight program for your needs.</p>
  <a class="btn btn-light" style="left:113px;top:373px;width:117px;height:36px">Explore</a>
  <a class="btn btn-outline" style="left:243px;top:373px;width:123px;height:36px">Learn more</a>
</header>

<section class="band">
  <div class="feature" style="left:112px">
    <svg viewBox="0 0 40 40"><path d="M4 28c6-4 12-4 18 0l10-6c2-1 4 1 2 3l-12 9H4"/><circle cx="20" cy="12" r="6"/></svg>
    <p class="label" style="margin:10px 0 6px">Flexible ownership options available</p>
    <p class="body">Choose from a variety of ownership programs and enjoy the freedom to fly on your own terms.</p>
  </div>
  <div class="feature" style="left:469px">
    <svg viewBox="0 0 40 40"><circle cx="16" cy="10" r="6"/><path d="M4 34c0-8 6-13 12-13"/><rect x="20" y="22" width="16" height="12"/><path d="M20 27h16"/></svg>
    <p class="label" style="margin:10px 0 6px">Convenient jet card programs</p>
    <p class="body">Access a fleet of private jets with our exclusive jet card programs, offering flexibility and convenience.</p>
  </div>
  <div class="feature" style="left:826px">
    <svg viewBox="0 0 40 40"><path d="M8 30l10-10 4 4-10 10z"/><path d="M20 18l8-8 4 4-8 8"/><path d="M26 4l2 3M32 8l3 2"/></svg>
    <p class="label" style="margin:10px 0 6px">Flexible lease programs</p>
    <p class="body">Experience the luxury of private jet travel without the commitment with our flexible lease programs.</p>
  </div>
</section>

<section class="ownership">
  <div class="photo" role="img" aria-label="Private jet with airstair lowered on the tarmac" style="left:113px;top:50px;width:258px;height:336px;background:linear-gradient(160deg,#9fb2c8 0%,#dfe3e6 45%,#7a7f86 100%)"></div>
  <div class="photo" role="img" aria-label="Cream leather seats inside a private jet cabin" style="left:284px;top:250px;width:245px;height:230px;background:linear-gradient(180deg,#f4efe6 0%,#d8cdbb 50%,#8b7b68 100%)"></div>
  <p class="abs eyebrow" style="left:589px;top:131px">Discover</p>
  <h2 class="abs display" style="left:588px;top:152px;font-size:29px;line-height:37px">Experience the luxury of<br>fractional jet ownership</h2>
  <p class="abs body" style="left:589px;top:246px;width:440px;font-size:10px">With Velorane's fractional jet ownership program, you can enjoy the benefits of private jet travel without the hassle and expense of owning a whole aircraft. Our program offers flexibility, convenience, and access to a fleet of luxurious jets, allowing you to travel in style and comfort.</p>
  <div class="abs radio" style="left:589px;top:331px">Flexible Ownership Options</div>
  <div class="abs radio" style="left:765px;top:331px">Convenient Booking Process</div>
  <div class="abs radio" style="left:947px;top:331px">Luxurious Fleet of Jets</div>
  <a class="btn btn-light" style="left:589px;top:366px;width:120px">Learn more</a>
  <a class="btn btn-outline" style="left:722px;top:366px;width:115px">Sign up</a>
</section>

<section class="services">
  <p class="abs eyebrow" style="left:112px;top:62px">Luxury</p>
  <h2 class="abs display" style="left:111px;top:82px;font-size:29px;line-height:37px">Experience the ultimate in<br>private jet travel</h2>
  <p class="abs body" style="left:609px;top:65px;width:480px;font-size:10px">Velorane offers a wide range of exclusive services to meet your private jet travel needs. From fractional jet ownership to on-demand charter flights, we provide the highest level of luxury and convenience.</p>
  <a class="btn btn-light" style="left:609px;top:118px;width:120px">Learn more</a>
  <a class="btn btn-outline" style="left:742px;top:118px;width:113px">Sign up</a>
  <div class="card" style="left:113px">
    <svg viewBox="0 0 34 34"><circle cx="17" cy="12" r="8"/><path d="M12 19l-3 12 8-4 8 4-3-12"/></svg>
    <p class="label" style="margin-bottom:8px">On-demand charter</p>
    <p class="body" style="font-size:10px">Fly anywhere, anytime with our on-demand charter service.</p>
  </div>
  <div class="card" style="left:443px">
    <svg viewBox="0 0 34 34"><circle cx="17" cy="17" r="14"/><ellipse cx="17" cy="17" rx="6" ry="14"/><path d="M3 17h28M6 9h22M6 25h22"/></svg>
    <p class="label" style="margin-bottom:8px">Global medical response &amp; recovery</p>
    <p class="body" style="font-size:10px">We provide specialized medical transportation services worldwide.</p>
  </div>
  <div class="card" style="left:772px">
    <svg viewBox="0 0 34 34"><circle cx="23" cy="10" r="6"/><path d="M19 14L5 28l3 3M9 24l3 3"/></svg>
    <p class="label" style="margin-bottom:8px">Fractional jet ownership</p>
    <p class="body" style="font-size:10px">Enjoy the benefits of owning a private jet without the hassles.</p>
  </div>
</section>

<section class="cta-light">
  <div class="photo" role="img" aria-label="Soft white clouds seen from above"></div>
  <h2 class="abs display" style="left:0;width:1200px;text-align:center;top:61px;font-size:29px;color:var(--dark-text)">Experience luxury travel like never before</h2>
  <p class="abs" style="left:0;width:1200px;text-align:center;top:108px;font-size:10px;color:var(--dark-text)">Contact us today to book your exclusive jet experience</p>
  <a class="btn btn-dark" style="left:476px;top:138px;width:120px">Learn more</a>
  <a class="btn btn-outline-dark" style="left:609px;top:138px;width:115px;background:#fff">Sign up</a>
</section>

<section class="luxury">
  <div class="photo sky" role="img" aria-label="Bright cloudscape behind the aircraft"></div>
  <div class="photo jet" role="img" aria-label="Silver private jet banking through the sky"></div>
  <p class="abs eyebrow" style="left:112px;top:116px">Experience</p>
  <h2 class="abs display" style="left:111px;top:134px;font-size:29px;line-height:37px">Unparalleled luxury and<br>convenience for private aviation</h2>
  <p class="abs body" style="left:113px;top:225px;width:480px;font-size:10px">Discover the ultimate in luxury and convenience with Velorane. Our exclusive private aviation solutions provide you with unparalleled access to the world of private jets, ensuring a seamless and extraordinary travel experience.</p>
  <div class="abs radio" style="left:113px;top:292px;font-weight:700">CONVENIENCE</div>
  <p class="abs body" style="left:130px;top:310px;width:210px;font-size:10px">Enjoy hassle-free travel with our flexible scheduling and personalized services.</p>
  <div class="abs radio" style="left:369px;top:292px;font-weight:700">LUXURY</div>
  <p class="abs body" style="left:386px;top:310px;width:210px;font-size:10px">Indulge in the lavish amenities and exquisite interiors of our private jets.</p>
  <a class="btn btn-light" style="left:113px;top:368px;width:118px">Learn more</a>
  <a class="btn btn-outline" style="left:245px;top:368px;width:114px">Sign up</a>
</section>

<section class="faq">
  <div class="photo" role="img" aria-label="Close view of a jet airstair and fuselage at sunset"></div>
  <h2 class="abs display" style="left:527px;top:112px;font-size:29px">Frequently</h2>
  <p class="abs body" style="left:528px;top:158px;font-size:10px">Find answers to common questions about Velorane's services and programs.</p>
  <div class="faq-item" style="top:192px"><div class="faq-q">What is Velorane?<b>+</b></div></div>
  <div class="faq-item" style="top:244px;height:107px">
    <div class="faq-q" style="height:30px;padding-top:6px">How it works?<b>−</b></div>
    <p class="body" style="font-size:9.5px;line-height:14px">Velorane works by allowing customers to purchase fractional ownership of a private jet, join jet card programs for a set number of flight hours, lease a private jet for a specific period, or access our all access and helicopter programs. We also offer charter flights where customers can book individual seats on private jets.</p>
  </div>
  <div class="faq-item" style="top:364px"><div class="faq-q">Why choose Velorane?<b>+</b></div></div>
  <div class="faq-item" style="top:417px"><div class="faq-q">How to book?<b>+</b></div></div>
  <div class="faq-item" style="top:469px"><div class="faq-q">What are the benefits?<b>+</b></div></div>
  <p class="abs" style="left:528px;top:532px;font-size:11px;font-weight:700;color:var(--white)">STILL HAVE QUESTIONS?</p>
  <p class="abs body" style="left:528px;top:550px;font-size:10px">Contact us for more information.</p>
  <a class="btn btn-light" style="left:528px;top:582px;width:117px">Learn more</a>
  <a class="btn btn-outline" style="left:660px;top:582px;width:115px">Sign up</a>
</section>

<section class="testimonial">
  <div class="photo" role="img" aria-label="Portrait of a businessman in a grey suit walking beside a private jet"></div>
  <p class="abs display" style="left:112px;top:126px;width:500px;font-size:22px;line-height:30px">Velorane's services have exceeded my expectations. The convenience and luxury of flying with them is unmatched.</p>
  <svg class="abs" style="left:113px;top:238px" width="110" height="16" viewBox="0 0 110 16" fill="#fff">
    <g id="star"><path d="M8 0l2.4 5 5.4.6-4 3.7 1.1 5.3L8 12 3.1 14.6 4.2 9.3 0.2 5.6 5.6 5z"/></g>
    <use href="#star" x="22"/><use href="#star" x="44"/><use href="#star" x="66"/><use href="#star" x="88"/>
  </svg>
  <p class="abs" style="left:113px;top:283px;font-family:'Saira',sans-serif;font-size:20px;color:var(--white)">Marcus Hale</p>
  <p class="abs body" style="left:113px;top:312px;font-size:9.5px">CEO, Halvern Group</p>
  <div class="abs" style="left:254px;top:283px;width:1px;height:46px;background:var(--muted)"></div>
  <p class="abs" style="left:292px;top:298px;font-size:14px;font-weight:700;color:var(--white)">Stratowell</p>
  <div class="arrows">
    <span><svg width="26" height="10" viewBox="0 0 26 10" stroke="#fff" fill="none"><path d="M25 5H1M5 1L1 5l4 4"/></svg></span>
    <span><svg width="26" height="10" viewBox="0 0 26 10" stroke="#fff" fill="none"><path d="M1 5h24M21 1l4 4-4 4"/></svg></span>
  </div>
</section>

<section class="cta-dark">
  <div class="photo" role="img" aria-label="Private jet on the apron in warm evening light" style="left:0;top:0;width:1200px;height:257px;background:radial-gradient(ellipse at 55% 80%,rgba(120,95,60,.45) 0%,rgba(0,0,0,0) 60%)"></div>
  <h2 class="abs display" style="left:0;width:1200px;text-align:center;top:52px;font-size:29px">Experience luxury travel like never before</h2>
  <p class="abs" style="left:299px;width:605px;text-align:center;top:98px;font-size:10px;line-height:12px;font-weight:600;color:var(--white)">Discover the ultimate in private jet travel with Velorane. Whether you're looking for fractional jet ownership, jet card programs, private jet lease programs, all access programs, helicopter access programs, or by the seat charter flights, we have the perfect solution for your travel needs.</p>
  <a class="btn btn-light" style="left:476px;top:152px;width:120px">Book</a>
  <a class="btn btn-outline" style="left:609px;top:152px;width:115px">Contact</a>
</section>

<footer class="footer">
  <div class="abs brand" style="left:112px;top:48px">Velorane<i></i></div>
  <p class="abs" style="left:112px;top:117px;font-size:9.5px;color:var(--white)">FOLLOW US:</p>
  <div class="social" style="left:112px;top:135px"></div>
  <div class="social" style="left:143px;top:135px"></div>
  <div class="social" style="left:174px;top:135px"></div>
  <div class="social" style="left:206px;top:135px"></div>
  <div class="abs" style="left:356px;top:50px"><h4>About us</h4><ul><li>Charter</li><li>Fleet</li><li>Destinations</li><li>Pricing</li><li>Contact</li></ul></div>
  <div class="abs" style="left:501px;top:50px"><h4>Services</h4><ul><li>Private Jets</li><li>Helicopters</li><li>Jet Cards</li><li>Membership</li><li>FAQ</li></ul></div>
  <div class="abs" style="left:643px;top:50px"><h4>Terms</h4><ul><li>Privacy</li><li>Careers</li><li>Press</li><li>Blog</li><li>Support</li></ul></div>
  <div class="abs" style="left:772px;top:50px;width:315px">
    <h4>Subscribe to our newsletter</h4>
    <p style="font-size:10px;color:var(--white)">Join our mailing list for the latest updates.</p>
  </div>
  <div class="abs" style="left:772px;top:96px;width:211px;height:32px;border:1px solid var(--white);font-size:9.5px;color:var(--muted);padding:10px 12px">Enter Your Email</div>
  <a class="btn btn-light" style="left:996px;top:96px;width:91px;height:32px">Subscribe</a>
  <p class="abs" style="left:772px;top:140px;width:315px;font-size:9.5px;line-height:13px;color:var(--white)">By subscribing, you agree to our Privacy Policy and consent to receive updates</p>
  <div class="abs" style="left:0;top:212px;width:1200px;height:1px;background:#5a5a5a"></div>
  <div class="abs legal" style="left:0;top:238px;width:1200px;display:flex;justify-content:center;gap:28px">
    <a>© 2024 Velorane. All rights reserved.</a><a>Privacy Policy</a><a>Terms of Service</a><a>Cookie Settings</a>
  </div>
</footer>

</body>
</html>
```